High-end law practice specializing in closely held business succession planning and complex estates

Solo practitioner whose practice specializes in high-net worth, Succession & Estate Planning needs muliple versions of letterhead black and white, please. Letterhead should incorporate slogan, "Guarding Your Family Legacy is my Business," for one and "Succession & Estate Planning"; third with no slogan. All for The Law Office of Marcy Lynn Pettibone, PC, 418 Cedar Hollow Ln., Carrow Point, Virginia 23648, Tel. 757-555-0142 Fax tbd email: marcy@mlplawgroup.example; Marcy Lynn Pettibone, Esq., principal, licensed in VA, MD, NC
Updates

Project Deadline Extended
Reason: My internet service went down and I can only view designs on my smart phone -- it's just too hard to review. So sorry! Working with my ISP now. Please be patient!

Target Market(s)

High net worth clients with Succession & Estate Planning needs, family businesses, family farmers, family foresters -- people with unique estate/succession planning needs who need a specialist who understands them.

Industry/Entity Type

Business

Font styles to use
Script

Requirements
Must have
• A high-end look and feel, connoting trustworthiness, special knowledge, and expertise.

```html
<!DOCTYPE html>
<html lang="en">
<head>
<meta charset="utf-8">
<title>Letterhead – The Law Office of Marcy Lynn Pettibone, PC</title>
<link rel="stylesheet" href="https://fonts.googleapis.com/css2?family=Arimo:wght@400;700&family=Open+Sans:wght@400;700&display=swap">
<style>
  :root {
    --backdrop: #e9e9e9;
    --paper: #ffffff;
    --ink: #111111;
    --rule: #222222;
    --pill-text: #ffffff;
  }
  * { margin: 0; padding: 0; box-sizing: border-box; }
  html, body {
    width: 1200px;
    height: 936px;
    overflow: hidden;
    background: var(--backdrop);
  }
  .canvas {
    position: relative;
    width: 1200px;
    height: 936px;
  }
  .letterhead {
    position: absolute;
    left: 289px;
    top: 28px;
    width: 622px;
    height: 880px;
    background: var(--paper);
    box-shadow: 0 2px 8px rgba(0,0,0,0.12);
    color: var(--ink);
  }
  .masthead {
    position: absolute;
    left: 40px;
    top: 44px;
    text-align: center;
    font-family: "Arimo", Arial, sans-serif;
  }
  .firm-name {
    font-weight: 700;
    font-size: 15px;
    line-height: 1.1;
    letter-spacing: 0.2px;
    text-transform: uppercase;
  }
  .principal {
    font-size: 10.5px;
    line-height: 1.25;
    margin-top: 3px;
  }
  .specialty {
    font-size: 10.5px;
    line-height: 1.2;
  }
  .footer-frame {
    position: absolute;
    left: 0;
    top: 0;
    width: 622px;
    height: 880px;
  }
  .contact {
    position: absolute;
    right: 26px;
    bottom: 62px;
    text-align: right;
    font-family: "Open Sans", Arial, sans-serif;
    font-style: normal;
    font-size: 10px;
    line-height: 1.45;
  }
  .contact .label { font-weight: 700; }
  .slogan {
    position: absolute;
    right: 24px;
    bottom: 40px;
    background: var(--ink);
    color: var(--pill-text);
    font-family: "Open Sans", Arial, sans-serif;
    font-size: 10.5px;
    line-height: 1;
    padding: 5px 12px 6px;
    border-radius: 10px;
    white-space: nowrap;
  }
</style>
</head>
<body>
<div class="canvas">
  <section class="letterhead">
    <header class="masthead">
      <div class="firm-name">The Law Office<br>of Marcy Lynn Pettibone, PC</div>
      <div class="principal">Marcy Lynn Pettibone, Esq., principal, licensed in VA, MD, NC</div>
      <div class="specialty">Succession &amp; Estate Planning</div>
    </header>

    <svg class="footer-frame" viewBox="0 0 622 880" aria-hidden="true">
      <line x1="22" y1="830" x2="622" y2="830" stroke="var(--rule)" stroke-width="1"/>
      <line x1="22" y1="830" x2="22" y2="880" stroke="var(--rule)" stroke-width="1"/>
    </svg>

    <address class="contact">
      418 Cedar Hollow Ln.,<br>
      Carrow Point, Virginia 23648<br>
      <span class="label">T</span>: 757-555-0142 | <span class="label">F</span>: 757-555-0199 | <span class="label">E</span>: marcy@mlplawgroup.example
    </address>
    <div class="slogan">Guarding Your Family Legacy is my Business</div>
  </section>
</div>
</body>
</html>
```